Print materials for 3-star hotel

We are changing up our print materials (notepads, letterheads, key card jackets, small flyer for the room rates) We are a 3 star business hotel in the Philippines and have mainly used grey tones and clean, simple lines. See attached photos for logo and hotel interior photos.

Target Market(s)

Business

Contact Information for Business Card

Corvale Terrace Hotel
Lindwell Banca Avenue corner Tolenta St Cebu City 6000 Philippines
Tel: +63 32 481 7302
Mobile: +63 917 648 2095
www.corvaleterracehotel.example

Font styles to use
Serif
Sans Serif

Requirements
Must have
• Simple
• Readable font and font size
Nice to have
• Neutral colors, grey and taupes
Should not have
• No purples and bright blues

```html
<!DOCTYPE html>
<html lang="en">
<head>
<meta charset="utf-8">
<title>Corvale Terrace Hotel – Business Card</title>
<link rel="stylesheet" href="https://fonts.googleapis.com/css2?family=Cinzel:wght@400&family=Roboto:wght@400;500&display=swap">
<style>
  :root {
    --backdrop: #e3e3e3;
    --card-taupe: #b6a68b;
    --ink-light: #f6f2ec;
    --rule: #f1ece4;
  }
  * { margin: 0; padding: 0; box-sizing: border-box; }
  html, body {
    width: 1200px; height: 960px; overflow: hidden;
    background: var(--backdrop);
  }
  .canvas { position: relative; width: 1200px; height: 960px; }

  .card {
    position: absolute;
    width: 601px; height: 343px;
    background: var(--card-taupe);
    color: var(--ink-light);
  }
  .card--front { left: 314px; top: 113px; }
  .card--back  { left: 311px; top: 472px; width: 600px; }

  .brand {
    position: absolute; left: 36px; top: 40px; width: 220px;
    text-align: center;
    font-family: "Cinzel", serif; font-weight: 400;
    color: var(--ink-light);
  }
  .brand__square {
    display: block; width: 30px; height: 30px;
    margin: 0 auto 14px; background: var(--ink-light);
  }
  .brand__name { font-size: 17px; letter-spacing: 2.4px; line-height: 1.1; }
  .brand__sub  { font-size: 13px; letter-spacing: 4px; line-height: 1.3; }

  .person {
    position: absolute; right: 33px; top: 173px; text-align: right;
  }
  .person__name {
    font-family: "Cinzel", serif; font-size: 22px; letter-spacing: .5px; line-height: 1.1;
  }
  .person__title {
    font-family: "Roboto", sans-serif; font-weight: 500; font-size: 14px; margin-top: 2px;
  }
  .divider {
    position: absolute; left: 157px; top: 228px; width: 407px; height: 1px;
    background: var(--rule);
  }

  .contacts {
    position: absolute; left: 38px; top: 219px; list-style: none;
    font-family: "Roboto", sans-serif; font-size: 14px; line-height: 19px;
  }
  .contacts li { display: flex; align-items: center; gap: 8px; }
  .contacts svg { width: 14px; height: 14px; fill: var(--ink-light); flex: none; }

  .address {
    position: absolute; right: 36px; top: 276px; text-align: right;
    font-family: "Roboto", sans-serif; font-size: 14px; line-height: 18px;
  }

  .back-brand {
    position: absolute; right: 38px; top: 216px; width: 200px;
    text-align: center; color: var(--ink-light);
  }
  .back-brand__square {
    display: block; width: 40px; height: 40px; margin: 0 auto 12px;
    background: var(--ink-light);
  }
  .back-brand__name {
    font-family: "Cinzel", serif; font-size: 13px; letter-spacing: 2px;
  }
  .back-brand__web {
    font-family: "Roboto", sans-serif; font-size: 14px; letter-spacing: 2.4px; margin-top: 4px;
  }
</style>
</head>
<body>
<main class="canvas">

  <section class="card card--front" aria-label="Business card front">
    <div class="brand">
      <span class="brand__square"></span>
      <div class="brand__name">CORVALE TERRACE</div>
      <div class="brand__sub">HOTEL</div>
    </div>

    <div class="person">
      <div class="person__name">MARCO DELANTAR</div>
      <div class="person__title">CEO/Founder</div>
    </div>
    <div class="divider"></div>

    <ul class="contacts">
      <li>
        <svg viewBox="0 0 24 24" aria-hidden="true"><path d="M6.6 10.8a15.1 15.1 0 0 0 6.6 6.6l2.2-2.2c.3-.3.7-.4 1-.2 1.1.4 2.3.6 3.6.6.6 0 1 .4 1 1V20c0 .6-.4 1-1 1A17 17 0 0 1 3 4c0-.6.4-1 1-1h3.5c.6 0 1 .4 1 1 0 1.3.2 2.5.6 3.6.1.3 0 .7-.2 1z"/></svg>
        632 481 7302
      </li>
      <li>
        <svg viewBox="0 0 24 24" aria-hidden="true"><path d="M7 1h10a2 2 0 0 1 2 2v18a2 2 0 0 1-2 2H7a2 2 0 0 1-2-2V3a2 2 0 0 1 2-2zm0 3v14h10V4zm5 15.5a1.2 1.2 0 1 0 0 2.4 1.2 1.2 0 0 0 0-2.4z"/></svg>
        917 648 2095
      </li>
      <li>
        <svg viewBox="0 0 24 24" aria-hidden="true"><path d="M6 2h12v6H6zM3 9h18a2 2 0 0 1 2 2v7h-4v4H5v-4H1v-7a2 2 0 0 1 2-2zm4 7v4h10v-4z"/></svg>
        632 481 7310
      </li>
      <li>
        <svg viewBox="0 0 24 24" aria-hidden="true"><path d="M2 5h20v14H2zm2 2v.5l8 5 8-5V7l-8 5z"/></svg>
        desk@corvale.example
      </li>
      <li>
        <svg viewBox="0 0 24 24" aria-hidden="true"><path d="M12 2a10 10 0 1 0 0 20 10 10 0 0 0 0-20zm-1 17.9A8 8 0 0 1 4.2 10.4L9 15v1a2 2 0 0 0 2 2zm6.9-2.5A2 2 0 0 0 16 16h-1v-3a1 1 0 0 0-1-1H8v-2h2a1 1 0 0 0 1-1V7h2a2 2 0 0 0 2-2v-.4a8 8 0 0 1 2.9 12.8z"/></svg>
        www.corvale.example
      </li>
    </ul>

    <address class="address" style="font-style:normal">
      Lindwell Banca Avenue<br>
      Cebu City 6000 Philippines
    </address>
  </section>

  <section class="card card--back" aria-label="Business card back">
    <div class="back-brand">
      <span class="back-brand__square"></span>
      <div class="back-brand__name">CORVALE TERRACE</div>
      <div class="back-brand__web">www.corvale.example</div>
    </div>
  </section>

</main>
</body>
</html>
```